Flat Belly Design Graphics for Social

I want to create 9 social media graphics (new Instagram size 4:5 (1080 x 1350 pixels) focusing on our Flat Belly Graphics, using the pics attached. Use the attached pics, NO RANDOM STOCK PHOTOGRAPHY. For the color scheme of the graphics, the color palette is attached. YOU MUST POST ALL 9 GRAPHICS IN ONE ENTRY.
Using the 3 titles below, create one set of graphics. 1) with all text, then for the others, use the pictures as detailed below in IMPORTANT:
1. Ten-Week Bright Morning Reboot
2. The Quick Garden Kitchen Menu Guide
3. Studio Habits for Lasting Energy Past Midlife - Zero Gym Needed
IMPORTANT:
Only use RK Pic 1 and RK Pic 2 with the title, Ten-Week Bright Morning Reboot
Only use meal plan1 and meal plan2 pics with the title, Quick Garden Kitchen Menu Guide
Only use studio habits 1 and studio habits 2 pics with the title, Studio Habits for Lasting Energy Past Midlife - Zero Gym Needed
women over 40

```html
<!DOCTYPE html>
<html lang="en">
<head>
<meta charset="utf-8">
<title>Flat Belly Social Graphics</title>
<link rel="stylesheet" href="https://fonts.googleapis.com/css2?family=Poppins:wght@500;600;700;800&family=Oswald:wght@600&display=swap">
<style>
  :root {
    --green: #2f4a45;
    --pink: #e394ad;
    --blush: #f7e5e8;
    --white: #ffffff;
    --wood: #3a2b24;
  }
  * { box-sizing: border-box; margin: 0; padding: 0; }
  html, body { width: 1200px; height: 404px; overflow: hidden; background: var(--white); }
  .canvas { position: relative; width: 1200px; height: 404px; font-family: "Poppins", sans-serif; }
  .post { position: absolute; top: 41px; width: 260px; height: 325px; overflow: hidden; }
  .post--reboot { left: 40px; background: var(--blush); }
  .post--studio { left: 331px; background: var(--green); }
  .post--menu { left: 622px; }
  .post--habits { left: 908px; background: var(--green); }

  /* Post 1 */
  .reboot-photo {
    position: absolute; inset: 0;
    background: radial-gradient(ellipse 55% 70% at 50% 45%, #e9d8d4 0%, #f3e1e3 60%, var(--blush) 100%);
  }
  .reboot-tab {
    position: absolute; left: 73px; top: 201px; width: 111px; height: 31px;
    background: var(--pink); color: var(--white);
    font-weight: 700; font-size: 19px; line-height: 31px; text-align: center; letter-spacing: .3px;
  }
  .reboot-box {
    position: absolute; left: 22px; top: 226px; width: 214px; height: 75px;
    background: var(--white); border: 4px solid var(--pink);
    display: flex; flex-direction: column; justify-content: center; align-items: center;
    color: var(--pink); font-weight: 700; font-size: 19px; line-height: 23px; text-align: center;
  }

  /* Post 2 */
  .studio-kicker {
    position: absolute; left: 13px; top: 17px; color: var(--white);
    font-weight: 700; font-size: 13.5px; letter-spacing: .2px; white-space: nowrap;
  }
  .studio-vertical {
    position: absolute; left: 0; top: 0; transform-origin: 0 0; transform: rotate(-90deg);
    white-space: nowrap;
  }
  .studio-title { left: 17px; top: 307px; color: var(--white); font-weight: 700; font-size: 25px; line-height: 1; letter-spacing: .4px; }
  .studio-sub {
    left: 49px; top: 283px; font-weight: 500; font-size: 17px; line-height: 1; letter-spacing: 1px;
    color: transparent; -webkit-text-stroke: 0.8px var(--white);
  }
  .studio-photo {
    position: absolute; left: 82px; top: 56px; width: 178px; height: 269px;
    background: linear-gradient(160deg, #c9a891 0%, #b98e74 45%, #8fa9bb 80%, #5b7594 100%);
    border-radius: 60px 40px 0 0;
  }

  /* Post 3 */
  .menu-photo {
    position: absolute; inset: 0;
    background:
      radial-gradient(ellipse 42% 40% at 50% 50%, var(--wood) 0%, var(--wood) 70%, transparent 100%),
      linear-gradient(135deg, #d9503b 0%, #e9a63a 25%, #5b8a3a 50%, #c94a3c 75%, #e57a4f 100%);
  }
  .menu-frame { position: absolute; left: 0; top: 0; }
  .menu-title {
    position: absolute; left: 0; right: 0; top: 107px;
    color: var(--white); text-align: center;
    font-family: "Oswald", sans-serif; font-weight: 600; font-size: 25px; line-height: 30px; letter-spacing: .5px;
  }

  /* Post 4 */
  .habits-arcs { position: absolute; inset: 0; }
  .habits-title {
    position: absolute; left: 0; right: 0; top: 74px;
    color: var(--white); text-align: center;
    font-weight: 800; font-size: 27px; line-height: 38px; letter-spacing: .5px;
  }
  .habits-band {
    position: absolute; left: 6px; top: 223px; width: 249px; height: 29px;
    background: var(--pink); color: var(--white); text-align: center;
    font-weight: 800; font-size: 21px; line-height: 29px; letter-spacing: .3px;
  }
</style>
</head>
<body>
<main class="canvas">

  <section class="post post--reboot">
    <div class="reboot-photo" role="img" aria-label="Smiling woman in a white sweater pointing down at the title, on a soft pink background"></div>
    <div class="reboot-box"><span>BRIGHT MORNING</span><span>REBOOT</span></div>
    <div class="reboot-tab">TEN-WEEK</div>
  </section>

  <section class="post post--studio">
    <p class="studio-kicker">STUDIO HABITS FOR LASTING</p>
    <p class="studio-vertical studio-title">ENERGY PAST MIDLIFE</p>
    <p class="studio-vertical studio-sub">ZERO GYM NEEDED</p>
    <div class="studio-photo" role="img" aria-label="Two women, one whispering a secret to the other who looks surprised"></div>
  </section>

  <section class="post post--menu">
    <div class="menu-photo" role="img" aria-label="Fresh fruit, vegetables, fish and meat arranged around a dark wooden board"></div>
    <svg class="menu-frame" width="260" height="325" viewBox="0 0 260 325" aria-hidden="true">
      <g fill="none" stroke="#ffffff" stroke-width="1.2">
        <polyline points="78,130 78,95 181,95 181,130"/>
        <polyline points="78,218 78,233 181,233 181,218"/>
      </g>
    </svg>
    <h2 class="menu-title">THE<br>QUICK GARDEN<br>KITCHEN MENU<br>GUIDE</h2>
  </section>

  <section class="post post--habits">
    <svg class="habits-arcs" width="260" height="325" viewBox="0 0 260 325" aria-hidden="true">
      <g fill="none">
        <path d="M 0 42 A 42 42 0 0 0 42 0" stroke="var(--pink)" stroke-width="4"/>
        <path d="M 0 49 A 49 49 0 0 0 49 0" stroke="#ffffff" stroke-width="1"/>
        <path d="M 218 325 A 42 42 0 0 1 260 283" stroke="var(--pink)" stroke-width="4"/>
        <path d="M 211 325 A 49 49 0 0 1 260 276" stroke="#ffffff" stroke-width="1"/>
      </g>
    </svg>
    <h2 class="habits-title">STUDIO HABITS<br>FOR LASTING<br>ENERGY PAST<br>MIDLIFE – ZERO</h2>
    <div class="habits-band">GYM NEEDED</div>
  </section>

</main>
</body>
</html>
```